Business Card for Olive Drift-Eco Friendly Organic Clothing Brand

We are looking for an amazing business card for our eco friendly, organic clothing brand. We are thinking maybe a business card with a peel off sticker on the back, since our hanging clothing tag is a peel off sticker on the back. I will attach our hang tag so we can make sure we stay in line with our design. I've also attached a bag we are doing because I do like the scattered emblem look as well.

```html
<!DOCTYPE html>
<html lang="en">
<head>
<meta charset="UTF-8">
<title>Olive Drift – Business Card</title>
<link rel="stylesheet" href="https://fonts.googleapis.com/css2?family=Montserrat:wght@500;600&family=Open+Sans:wght@400;600&display=swap">
<style>
  :root {
    --stage: #2a2b2e;
    --card-dark: #22231f;
    --card-dark-2: #33342c;
    --card-light: #ffffff;
    --gold: #c9a13c;
    --gold-soft: #d8b75e;
    --ink: #2b2b2b;
    --rule: #bdbdbd;
  }
  html, body {
    margin: 0;
    width: 1200px;
    height: 864px;
    overflow: hidden;
    background: var(--stage);
  }
  .canvas {
    position: relative;
    width: 1200px;
    height: 864px;
  }
  .card {
    position: absolute;
    border-radius: 3px;
    box-shadow: 0 10px 24px rgba(0,0,0,0.35);
    overflow: hidden;
  }

  /* Back of card */
  .card-back {
    left: 170px;
    top: 100px;
    width: 540px;
    height: 309px;
    background: var(--card-dark);
  }
  .card-back .scatter-pattern {
    position: absolute;
    inset: 0;
    background:
      radial-gradient(ellipse at 30% 30%, rgba(201,161,60,0.28), transparent 55%),
      radial-gradient(ellipse at 75% 40%, rgba(201,161,60,0.22), transparent 55%),
      linear-gradient(160deg, var(--card-dark-2), var(--card-dark));
  }
  .card-back .brand-name {
    position: absolute;
    left: 0;
    right: 0;
    bottom: 52px;
    text-align: center;
    font-family: "Montserrat", sans-serif;
    font-weight: 600;
    font-size: 50px;
    color: var(--gold);
    letter-spacing: 0.5px;
  }

  /* Front of card */
  .card-front {
    left: 480px;
    top: 440px;
    width: 560px;
    height: 320px;
    background: var(--card-light);
  }
  .holder {
    position: absolute;
    left: 58px;
    top: 116px;
  }
  .holder-name {
    font-family: "Montserrat", sans-serif;
    font-weight: 600;
    font-size: 19px;
    color: var(--gold);
    margin: 0;
  }
  .holder-title {
    font-family: "Open Sans", sans-serif;
    font-size: 12.5px;
    color: var(--ink);
    margin: 1px 0 0;
  }
  .divider {
    position: absolute;
    left: 230px;
    right: 40px;
    top: 160px;
    height: 1px;
    background: var(--rule);
  }
  .brand-tag {
    position: absolute;
    right: 40px;
    top: 50px;
    display: flex;
    align-items: center;
    gap: 10px;
  }
  .brand-tag .mark {
    width: 16px;
    height: 16px;
    background: var(--gold);
  }
  .brand-tag .brand-name {
    font-family: "Montserrat", sans-serif;
    font-weight: 600;
    font-size: 28px;
    color: var(--gold);
  }
  .brand-url {
    position: absolute;
    right: 66px;
    top: 92px;
    font-family: "Open Sans", sans-serif;
    font-size: 9px;
    color: var(--ink);
  }
  .contacts {
    position: absolute;
    right: 36px;
    top: 196px;
    margin: 0;
    padding: 0;
    list-style: none;
    font-family: "Open Sans", sans-serif;
    font-size: 14px;
    color: var(--ink);
    text-align: right;
  }
  .contacts li {
    display: flex;
    justify-content: flex-end;
    align-items: center;
    gap: 9px;
    height: 21px;
  }
  .contacts svg {
    width: 11px;
    height: 11px;
    fill: none;
    stroke: var(--gold-soft);
    stroke-width: 1.6;
  }
</style>
</head>
<body>
<main class="canvas">

  <section class="card card-back">
    <div class="scatter-pattern" role="img" aria-label="Scattered gold words and symbols: peace, love, namaste, om, live, inspire, hearts and peace signs"></div>
    <div class="brand-name">Olive Drift</div>
  </section>

  <section class="card card-front">
    <div class="brand-tag">
      <span class="mark"></span>
      <span class="brand-name">Olive Drift</span>
    </div>
    <div class="brand-url">www.olivedrift.co</div>

    <div class="holder">
      <p class="holder-name">Daniel Hayes</p>
      <p class="holder-title">Managing Director</p>
    </div>
    <div class="divider"></div>

    <ul class="contacts">
      <li>044-555-0142
        <svg viewBox="0 0 12 12"><path d="M2 1.5l2.2 0 1 2.5-1.3 1a6 6 0 0 0 3.1 3.1l1-1.3 2.5 1v2.2A1 1 0 0 1 9.5 11 8.5 8.5 0 0 1 1 2.5a1 1 0 0 1 1-1z"/></svg>
      </li>
      <li>123-555-0187
        <svg viewBox="0 0 12 12"><rect x="1.5" y="5" width="9" height="5"/><path d="M3.5 5V1.5h5V5"/></svg>
      </li>
      <li>123-555-0187
        <svg viewBox="0 0 12 12"><rect x="3" y="1" width="6" height="10" rx="1"/><path d="M5.5 9h1"/></svg>
      </li>
      <li>hello@olivedrift.co
        <svg viewBox="0 0 12 12"><rect x="1" y="2.5" width="10" height="7"/><path d="M1 2.5l5 4 5-4"/></svg>
      </li>
      <li>www.olivedrift.co
        <svg viewBox="0 0 12 12"><path d="M5 7l2-2"/><path d="M4.5 5.5L3 7a1.7 1.7 0 0 0 2.4 2.4L7 8"/><path d="M7.5 6.5L9 5A1.7 1.7 0 0 0 6.6 2.6L5 4"/></svg>
      </li>
    </ul>
  </section>

</main>
</body>
</html>
```